wealth management firm, professional group, new model

we have a logo that works but we need a card, white background using our colors...clean look

our tag line if can be used in

The Path From Saver To Steward

```html
<!DOCTYPE html>
<html lang="en">
<head>
<meta charset="utf-8">
<title>Arcvale Wealth Partners – Business Card</title>
<link rel="stylesheet" href="https://fonts.googleapis.com/css2?family=Montserrat:wght@400;500;700;800&display=swap">
<style>
  :root {
    --navy: #1b2a4a;
    --card: #ffffff;
    --backdrop: #f3ead6;
    --card-edge: #e6e1d6;
  }
  * { margin: 0; padding: 0; box-sizing: border-box; }
  html, body {
    width: 1200px;
    height: 896px;
    overflow: hidden;
  }
  body {
    background: var(--backdrop);
    font-family: "Montserrat", sans-serif;
    color: var(--navy);
    position: relative;
  }
  .card {
    position: absolute;
    top: 293px;
    width: 540px;
    height: 310px;
    background: var(--card);
    border: 1px solid var(--card-edge);
    display: flex;
    flex-direction: column;
    align-items: center;
    justify-content: center;
    text-align: center;
  }
  .card--front { left: 40px; }
  .card--back  { left: 620px; }

  .holder-name {
    font-weight: 800;
    font-size: 34px;
    letter-spacing: 0.08em;
    text-transform: uppercase;
    line-height: 1;
  }
  .holder-title {
    font-weight: 500;
    font-size: 19px;
    margin-top: 8px;
  }
  .tagline {
    font-weight: 700;
    font-size: 13px;
    letter-spacing: 0.04em;
    text-transform: uppercase;
    margin-top: 30px;
    padding-bottom: 6px;
    border-bottom: 3px solid var(--navy);
  }
  .contact {
    font-weight: 500;
    font-size: 16px;
    line-height: 1.45;
    margin-top: 28px;
  }
  .contact .divider { margin: 0 10px; }

  .brand-name {
    font-weight: 500;
    font-size: 58px;
    letter-spacing: 0.36em;
    margin-right: -0.36em;
    text-transform: uppercase;
    line-height: 1;
  }
  .brand-sub {
    font-weight: 500;
    font-size: 20px;
    letter-spacing: 0.2em;
    margin-right: -0.2em;
    text-transform: uppercase;
    margin-top: 18px;
  }
</style>
</head>
<body>
  <section class="card card--front">
    <h1 class="holder-name">Jordan Hale</h1>
    <p class="holder-title">Senior Wealth Advisor</p>
    <p class="tagline">The Path From Saver To Steward</p>
    <p class="contact">
      jordan@arcvalewealth.com<span class="divider">|</span>+1 (555) 018-4420<br>
      arcvalewealth.com
    </p>
  </section>

  <section class="card card--back">
    <p class="brand-name">Arcvale</p>
    <p class="brand-sub">Wealth Partners</p>
  </section>
</body>
</html>
```